Global (re)insurance broker needs a business card design

We need a classic business card for our company that is headquartered in SG, with offices in Malaysia and Dubai. We specialise in insurance and reinsurance broking and consultancy for our global clients.

```html
<!DOCTYPE html>
<html lang="en">
<head>
<meta charset="utf-8">
<title>Kelvora – Business Card</title>
<link rel="stylesheet" href="https://fonts.googleapis.com/css2?family=Open+Sans:wght@400;600;700&display=swap">
<style>
  :root {
    --brand-blue: #2547a3;
    --brand-blue-deep: #1d3a8c;
    --brand-blue-light: #3557b8;
    --brand-green: #b9d9b0;
    --card-white: #f5f5f5;
    --ink: #1c1c1c;
    --rule: #3a3a3a;
    --backdrop: #e6e7ea;
  }
  * { box-sizing: border-box; margin: 0; padding: 0; }
  html, body { width: 1200px; height: 780px; overflow: hidden; }
  body {
    background: var(--backdrop);
    font-family: "Open Sans", Arial, sans-serif;
    position: relative;
  }
  .card {
    position: absolute;
    top: 235px;
    width: 540px;
    height: 310px;
    overflow: hidden;
    box-shadow: 0 6px 18px rgba(0,0,0,0.18);
  }

  /* Front */
  .card-front { left: 45px; background: var(--card-white); }
  .front-wordmark {
    position: absolute;
    top: 38px;
    left: 215px;
    font-size: 56px;
    font-weight: 700;
    letter-spacing: 2px;
    color: var(--brand-blue);
    line-height: 1;
  }
  .holder {
    position: absolute;
    top: 150px;
    left: 30px;
  }
  .holder-name {
    font-size: 30px;
    font-weight: 700;
    line-height: 1.1;
    color: var(--brand-blue);
  }
  .holder-name .surname { color: var(--brand-green); }
  .holder-title {
    font-size: 16px;
    font-weight: 400;
    color: var(--ink);
    margin-top: 2px;
  }
  .divider {
    position: absolute;
    left: 262px;
    top: 150px;
    width: 1px;
    height: 96px;
    background: var(--rule);
  }
  .contacts {
    position: absolute;
    left: 282px;
    top: 162px;
    list-style: none;
  }
  .contacts li {
    display: flex;
    align-items: center;
    gap: 8px;
    font-size: 16px;
    color: var(--ink);
    line-height: 26px;
  }
  .contacts svg { width: 13px; height: 13px; flex: none; }
  .address-band {
    position: absolute;
    left: 0; right: 0; bottom: 0;
    height: 42px;
    background: var(--brand-blue);
    color: #fff;
    font-size: 15.5px;
    display: flex;
    align-items: center;
    padding-left: 30px;
  }

  /* Back */
  .card-back { left: 615px; background: var(--brand-blue); }
  .back-pattern {
    position: absolute;
    inset: 0;
    background: linear-gradient(115deg, var(--brand-blue-deep) 0%, var(--brand-blue) 50%, var(--brand-blue-light) 100%);
  }
  .back-wordmark {
    position: absolute;
    inset: 0;
    display: flex;
    align-items: center;
    justify-content: center;
    font-size: 64px;
    font-weight: 700;
    letter-spacing: 3px;
    color: #fff;
  }
</style>
</head>
<body>
  <section class="card card-front" aria-label="Business card front">
    <div class="front-wordmark">KELVORA</div>

    <div class="holder">
      <h1 class="holder-name">Mira <span class="surname">Hale</span></h1>
      <p class="holder-title">Chief Operating Officer</p>
    </div>

    <div class="divider"></div>

    <ul class="contacts">
      <li>
        <svg viewBox="0 0 14 14" aria-hidden="true"><rect x="3.5" y="0.8" width="7" height="12.4" rx="1.4" fill="none" stroke="#9cc694" stroke-width="1.2"/><circle cx="7" cy="11" r="0.8" fill="#9cc694"/></svg>
        +65 9000 4182
      </li>
      <li>
        <svg viewBox="0 0 14 14" aria-hidden="true"><circle cx="7" cy="7" r="6.3" fill="var(--brand-blue)"/><path d="M0.8 7h12.4M7 0.8c-2.4 2.6-2.4 9.8 0 12.4M7 0.8c2.4 2.6 2.4 9.8 0 12.4" fill="none" stroke="#fff" stroke-width="0.8"/></svg>
        www.kelvora.com
      </li>
      <li>
        <svg viewBox="0 0 14 14" aria-hidden="true"><rect x="0.8" y="2.8" width="12.4" height="8.6" rx="1" fill="#9cc694"/><path d="M1.2 3.4 7 8l5.8-4.6" fill="none" stroke="#fff" stroke-width="1"/></svg>
        mira@kelvora.com
      </li>
    </ul>

    <div class="address-band">22 Harbour Lane, Marina Tower #08-04, Singapore 018956</div>
  </section>

  <section class="card card-back" aria-label="Business card back">
    <div class="back-pattern" role="img" aria-label="Repeating pattern of the company name in tonal blues"></div>
    <div class="back-wordmark">KELVORA</div>
  </section>
</body>
</html>
```